Valmora Company needs a Business Card Design

We just opened our business recently and we need a business card design. Our basic product are clothes and accessories. We would like to see designs that use bright colors like pink, light blue and purple. In addition to that kindly include also our address in the business card which our main office is located in Los Angeles, California.
The final design should communicate that we have affordable price yet high quality brand.

Target Market(s)

young and middle age women

Industry/Entity Type

Business

Contact Information for Business Card

Valmora Apparel and Accessories 4873 North Bellcrest St. Los Angeles California
Tel: 555-318-6492

Logo Text

Valmora's Apparel and Accessories

Font styles to use
Serif

Requirements
Must have
• there should be a graphic of a sexy lady wearing an elegant dress at the upper left corner of the business card.

```html
<!DOCTYPE html>
<html lang="en">
<head>
<meta charset="utf-8">
<title>Valmora Apparel and Accessories – Business Card</title>
<link rel="stylesheet" href="https://fonts.googleapis.com/css2?family=Cormorant+Garamond:wght@500;600&family=UnifrakturMaguntia&display=swap">
<style>
  :root {
    --page-bg: #e9e6e8;
    --card-white: #f4f3f4;
    --card-white-shade: #dcdadc;
    --pearl-tone: #e6e4e6;
    --band-top: #7a4a60;
    --band-mid: #4a2b3a;
    --band-bottom: #221a1f;
    --logo-pink: #b8386a;
    --band-text: #f6eef2;
    --silhouette-dark: #1d1a1c;
    --silhouette-pink: #c85a8a;
  }
  * { margin: 0; padding: 0; box-sizing: border-box; }
  html, body {
    width: 1200px; height: 818px; overflow: hidden;
    background: var(--page-bg);
  }
  .canvas {
    position: relative; width: 1200px; height: 818px;
    display: flex; align-items: center; justify-content: center;
  }
  .business-card {
    position: relative; width: 1040px; height: 596px;
    border-radius: 34px; overflow: hidden;
    background: linear-gradient(180deg, var(--card-white) 0%, var(--card-white-shade) 100%);
    box-shadow: 0 14px 40px rgba(40, 20, 30, 0.25);
    font-family: "Cormorant Garamond", Georgia, serif;
  }
  .pearl-pattern {
    position: absolute; left: 0; top: 0; width: 100%; height: 330px;
    background: radial-gradient(ellipse at 45% 45%, #ffffff 0%, var(--pearl-tone) 55%, var(--card-white-shade) 100%);
    opacity: 0.9;
  }
  .model-illustration {
    position: absolute; left: 70px; top: 148px; width: 210px; height: 182px;
    border-radius: 90px 90px 8px 8px;
    background: linear-gradient(180deg, var(--silhouette-dark) 0%, #3a2530 60%, var(--silhouette-pink) 100%);
  }
  .brand {
    position: absolute; left: 390px; top: 52px; width: 560px;
    text-align: center; color: var(--logo-pink); font-weight: 500;
  }
  .brand-name {
    font-size: 74px; letter-spacing: 0.32em; line-height: 1;
    padding-left: 0.32em;
  }
  .brand-tagline {
    margin-top: 10px; font-size: 44px; letter-spacing: 0.02em; line-height: 1.1;
  }
  .contact-band {
    position: absolute; left: 0; top: 330px; width: 100%; height: 266px;
    background: linear-gradient(180deg, var(--band-top) 0%, var(--band-mid) 45%, var(--band-bottom) 100%);
    color: var(--band-text);
  }
  .person {
    position: absolute; left: 70px; top: 92px;
  }
  .person-name {
    font-family: "UnifrakturMaguntia", "Times New Roman", serif;
    font-size: 38px; line-height: 1.1;
  }
  .person-role {
    margin-top: 6px; font-size: 32px; font-weight: 600;
  }
  .contact-list {
    position: absolute; left: 430px; top: 52px; list-style: none;
  }
  .contact-item {
    display: flex; align-items: center; gap: 16px;
    font-size: 26px; font-weight: 600; line-height: 1.2;
    white-space: nowrap;
    margin-bottom: 30px;
  }
  .contact-icon { width: 22px; height: 26px; flex: none; }
</style>
</head>
<body>
<main class="canvas">
  <article class="business-card">
    <div class="pearl-pattern" role="img" aria-label="Faint decorative pattern of pearl strands and chains"></div>
    <div class="model-illustration" role="img" aria-label="Silhouette illustration of a seated woman in a pink outfit"></div>

    <header class="brand">
      <div class="brand-name">Valmora</div>
      <div class="brand-tagline">Apparel and Accessories</div>
    </header>

    <section class="contact-band">
      <div class="person">
        <div class="person-name">Your Name</div>
        <div class="person-role">Position</div>
      </div>
      <ul class="contact-list">
        <li class="contact-item">
          <svg class="contact-icon" viewBox="0 0 24 24" aria-hidden="true">
            <path fill="#f6eef2" d="M6.6 2.5c.6-.3 1.3 0 1.6.6l1.6 3.5c.3.6.1 1.2-.4 1.6l-1.6 1.2c1 2.2 2.8 4 5 5l1.2-1.6c.4-.5 1-.7 1.6-.4l3.5 1.6c.6.3.9 1 .6 1.6l-.9 2.3c-.3.7-1 1.1-1.7 1.1C9.7 19 5 14.3 5 7.1c0-.7.4-1.4 1.1-1.7z"/>
          </svg>
          <span>555-318-6492</span>
        </li>
        <li class="contact-item">
          <svg class="contact-icon" viewBox="0 0 24 28" aria-hidden="true">
            <path fill="#f6eef2" d="M12 1C6.5 1 3 5 3 9.8 3 16 12 27 12 27s9-11 9-17.2C21 5 17.5 1 12 1zm0 12a3.4 3.4 0 1 1 0-6.8 3.4 3.4 0 0 1 0 6.8z"/>
          </svg>
          <span>4873 North Bellcrest St. Los Angeles California</span>
        </li>
      </ul>
    </section>
  </article>
</main>
</body>
</html>
```